Business Card for Field Bloom-Eco Friendly Organic Clothing Brand

We are looking for an amazing business card for our eco friendly, organic clothing brand. We are thinking maybe a business card with a peel off sticker on the back, since our hanging clothing tag is a peel off sticker on the back. I will attach our hang tag so we can make sure we stay in line with our design. I've also attached a bag we are doing because I do like the scattered emblem look as well.

```html
<!DOCTYPE html>
<html lang="en">
<head>
<meta charset="UTF-8">
<title>Field Bloom — Business Card</title>
<link rel="stylesheet" href="https://fonts.googleapis.com/css2?family=Open+Sans:wght@400;600;700&family=Roboto+Slab:wght@700&display=swap">
<style>
  :root {
    --stage: #2b2c2e;
    --card-black: #111111;
    --card-white: #ffffff;
    --gold: #d4a935;
    --text-light: #f2f2f2;
    --pattern-dark: #1c1c1a;
  }
  * { margin: 0; padding: 0; box-sizing: border-box; }
  html, body { width: 1200px; height: 950px; overflow: hidden; }
  body {
    background: var(--stage);
    font-family: "Open Sans", Arial, sans-serif;
    position: relative;
  }
  .card {
    position: absolute;
    left: 250px;
    width: 700px;
    height: 400px;
    border-radius: 22px;
    overflow: hidden;
  }
  /* Back side */
  .card-back { top: 50px; background: var(--card-black); }
  .back-pattern {
    position: absolute; inset: 0;
    background: radial-gradient(ellipse at 40% 40%, #3a3320 0%, var(--pattern-dark) 60%, #0d0d0c 100%);
  }
  .brand-frame {
    position: absolute;
    left: 150px; top: 140px;
    width: 400px; height: 120px;
    border: 4px solid var(--gold);
    background: var(--card-black);
    display: flex; align-items: center; justify-content: center;
  }
  .brand-frame .brand-name {
    font-family: "Roboto Slab", Georgia, serif;
    font-weight: 700;
    font-size: 52px;
    color: var(--gold);
    white-space: nowrap;
  }
  /* Front side */
  .card-front { top: 500px; background: var(--card-white); }
  .front-shape { position: absolute; inset: 0; }
  .brand-tag {
    position: absolute;
    left: 60px; top: 166px;
    display: flex; align-items: center; gap: 14px;
  }
  .brand-tag .mark {
    width: 34px; height: 34px;
    background: var(--card-black);
  }
  .brand-tag .brand-name {
    font-weight: 700;
    font-size: 34px;
    color: var(--card-black);
    white-space: nowrap;
  }
  .contact {
    position: absolute;
    left: 420px; top: 92px;
    color: var(--text-light);
  }
  .contact .person { font-size: 24px; font-weight: 700; color: var(--gold); line-height: 1.1; }
  .contact .role { font-size: 17px; margin-bottom: 22px; }
  .contact .address { font-size: 16px; line-height: 1.35; margin-bottom: 4px; }
  .contact .line { display: flex; align-items: center; gap: 10px; font-size: 16px; line-height: 1.5; }
  .contact .line svg { width: 15px; height: 15px; flex: none; }
</style>
</head>
<body>

<section class="card card-back" aria-label="Card back">
  <div class="back-pattern" role="img" aria-label="Decorative gold word pattern on black"></div>
  <div class="brand-frame"><span class="brand-name">Field Bloom</span></div>
</section>

<section class="card card-front" aria-label="Card front">
  <svg class="front-shape" viewBox="0 0 700 400" preserveAspectRatio="none" aria-hidden="true">
    <path d="M380 0 H700 V400 H380 Q395 360 395 200 Q395 40 380 0 Z" fill="var(--card-black)"/>
    <path d="M380 0 Q395 40 395 200 Q395 360 380 400" fill="none" stroke="var(--gold)" stroke-width="5"/>
  </svg>

  <div class="brand-tag">
    <span class="mark"></span>
    <span class="brand-name">Field Bloom</span>
  </div>

  <div class="contact">
    <p class="person">Alex Marlow</p>
    <p class="role">President</p>
    <p class="address">1420 Cedar Hollow Lane<br>Brookvale, NY 11020</p>
    <p class="line">
      <svg viewBox="0 0 16 16"><path d="M3 2h3l1 4-2 1c1 2 2 3 4 4l1-2 4 1v3c0 1-1 1-1 1C7 14 2 9 2 3c0 0 0-1 1-1z" fill="var(--gold)"/></svg>
      555 0142 7781
    </p>
    <p class="line">
      <svg viewBox="0 0 16 16"><rect x="4" y="1" width="8" height="14" rx="1.5" fill="none" stroke="var(--gold)" stroke-width="1.6"/><circle cx="8" cy="12.5" r="1" fill="var(--gold)"/></svg>
      555 0198 3306
    </p>
    <p class="line">
      <svg viewBox="0 0 16 16"><rect x="1" y="6" width="14" height="8" rx="1" fill="var(--gold)"/><rect x="4" y="2" width="8" height="5" fill="none" stroke="var(--gold)" stroke-width="1.5"/></svg>
      555 0167 4412
    </p>
    <p class="line">
      <svg viewBox="0 0 16 16"><rect x="1" y="3" width="14" height="10" rx="1" fill="var(--gold)"/><path d="M1.5 3.5 8 9l6.5-5.5" fill="none" stroke="var(--card-black)" stroke-width="1.3"/></svg>
      info@fieldbloom.com
    </p>
  </div>
</section>

</body>
</html>
```